Flyer Design Project

I need a cool design that describes a new line of services I am selling. The final product should be a 8 1/2 by 11 and maximum two pages.

I am selling consulting services to learn to use web conferencing tools for business development, meeting and training.
Updates

Please use the file I have attached as a guide for your work. It is a document called "guide-quickofficehints" and I love its design.

Thanks

                                        Please substitute the new text availble and just uploaded in the FLYER. Please submit the FINAL version fo your design with TExt changes as well as improvements detailed in previous message. 

Target Market(s)

Entrepreneurs and classroom educators who wnats to explore a new way to teach (innovators not scared of technology)

Industry/Entity Type

Business

Requirements
Must have
• I would like to receive a final PDF with the content EDITABLE for minor edits (I have acrobat)
Logo should be included (attached)

PLEASE CHECK OUT ATTACHED DOCUMENT WHOSE DESIGN I LOVE.
IT is called "Guide quick-office hints". If you could follow that as a template to design mine that would be great!

```html
<!DOCTYPE html>
<html lang="en">
<head>
<meta charset="utf-8">
<title>Online Meeting Skills Services – Flyer</title>
<link rel="stylesheet" href="https://fonts.googleapis.com/css2?family=Open+Sans:wght@400;600;700;800&family=Arimo:wght@400;700&display=swap">
<style>
  :root{
    --orange:#e0641c;
    --orange-deep:#c24e10;
    --orange-soft:#f2a36a;
    --ink:#141414;
    --paper:#ffffff;
    --stage:#d9d6d1;
    --grey:#6b6b6b;
  }
  *{box-sizing:border-box;margin:0;padding:0}
  html,body{width:1200px;height:900px;overflow:hidden}
  body{background:var(--stage);font-family:"Arimo",Arial,sans-serif;color:var(--ink);position:relative}
  .page{position:absolute;top:94px;width:550px;height:712px;background:var(--paper);overflow:hidden;box-shadow:0 4px 14px rgba(0,0,0,.25)}
  .page--cover{left:30px}
  .page--inside{left:620px}
  .page svg.backdrop{position:absolute;inset:0;width:100%;height:100%}

  .brand{position:absolute;top:40px;right:34px;text-align:center}
  .brand__name{font-family:"Open Sans",sans-serif;font-weight:700;font-size:24px;letter-spacing:.5px;color:var(--ink);display:flex;align-items:center;gap:7px}
  .brand__mark{width:12px;height:12px;border-radius:50%;background:var(--orange)}
  .brand__tag{font-family:"Open Sans",sans-serif;font-size:11px;font-weight:600;color:var(--orange);margin-top:2px}
  .page--inside .brand{top:28px;right:30px}
  .page--inside .brand__name{font-size:18px}
  .page--inside .brand__tag{font-size:8.5px}

  .cover-title{position:absolute;left:38px;top:344px;width:270px;font-family:"Open Sans",sans-serif}
  .cover-title__main{color:var(--orange);font-weight:700;font-size:31px;line-height:1.18}
  .cover-title__sub{color:var(--paper);font-weight:400;font-size:29px;line-height:1.2;margin-top:6px}

  .inside-body{position:absolute;left:34px;right:34px;top:78px;font-size:7.6px;line-height:1.38}
  .inside-body h1{font-family:"Open Sans",sans-serif;font-size:11px;font-weight:800;color:var(--orange);letter-spacing:.3px;margin-bottom:9px}
  .inside-body h2{font-family:"Open Sans",sans-serif;font-size:11.5px;font-weight:700;line-height:1.25;margin-bottom:5px}
  .inside-body p{margin-bottom:5px}
  .inside-body ul{list-style:none;margin-bottom:8px}
  .inside-body li{padding-left:8px;position:relative;margin-bottom:1px}
  .inside-body li::before{content:"•";position:absolute;left:0}
  .section-lead{font-family:"Open Sans",sans-serif;font-size:11px;font-weight:700;line-height:1.25;margin:30px 0 8px}
  .offer{margin:0 0 8px 10px}
  .offer__name{font-weight:700;margin-bottom:2px}
  .platform-note{font-family:"Open Sans",sans-serif;font-size:10px;font-weight:700;line-height:1.25;margin:12px 0 6px}
  .contact{position:absolute;left:34px;bottom:20px;font-family:"Open Sans",sans-serif;font-size:10px;font-weight:700;color:var(--paper)}
</style>
</head>
<body>

<section class="page page--cover" aria-label="Flyer cover">
  <svg class="backdrop" viewBox="0 0 550 712" preserveAspectRatio="none" aria-hidden="true">
    <defs>
      <linearGradient id="swoosh" x1="0" y1="0" x2="1" y2="1">
        <stop offset="0" stop-color="#f7c39a"/>
        <stop offset=".5" stop-color="#e0641c"/>
        <stop offset="1" stop-color="#a63c08"/>
      </linearGradient>
      <linearGradient id="photoTone" x1="0" y1="0" x2="1" y2="1">
        <stop offset="0" stop-color="#f0a468"/>
        <stop offset=".55" stop-color="#d25a18"/>
        <stop offset="1" stop-color="#3a1a08"/>
      </linearGradient>
    </defs>
    <path d="M0 120 C120 170 230 260 300 360 L0 360 Z" fill="url(#swoosh)" opacity=".85"/>
    <path d="M0 40 C160 120 280 230 360 330 L330 340 C250 250 140 160 0 110 Z" fill="#f4b285" opacity=".7"/>
    <g role="img" aria-label="Photo of a hand typing on a laptop keyboard in warm orange light">
      <path d="M190 320 C330 290 460 300 550 330 L550 712 L190 712 Z" fill="url(#photoTone)"/>
    </g>
    <path d="M0 300 L0 712 L60 712 C40 600 40 420 90 300 Z" fill="url(#swoosh)"/>
    <circle cx="168" cy="430" r="172" fill="var(--ink)"/>
    <rect x="0" y="690" width="550" height="22" fill="var(--orange)"/>
  </svg>

  <div class="brand">
    <div class="brand__name"><span class="brand__mark"></span>Convergia Consulting</div>
    <div class="brand__tag">Learn. Connect. Grow.</div>
  </div>

  <div class="cover-title">
    <div class="cover-title__main">Online Meeting Skills Services:</div>
    <div class="cover-title__sub">It is just the beginning…</div>
  </div>
</section>

<section class="page page--inside" aria-label="Flyer services page">
  <svg class="backdrop" viewBox="0 0 550 712" preserveAspectRatio="none" aria-hidden="true">
    <path d="M0 280 C160 258 380 254 550 270 L550 712 L0 712 Z" fill="var(--orange)"/>
    <path d="M0 280 C160 258 380 254 550 270 L550 282 C380 266 160 270 0 294 Z" fill="var(--orange-deep)"/>
  </svg>

  <div class="brand">
    <div class="brand__name"><span class="brand__mark"></span>Convergia Consulting</div>
    <div class="brand__tag">Learn. Connect. Grow.</div>
  </div>

  <div class="inside-body">
    <h1>ONLINE MEETING SKILLS SERVICES</h1>
    <h2>What if your business can reach all the people already interested in learning what you know?</h2>
    <p>A different use of webinar technology: the first step towards a new way of thinking about your marketplace and your clients.</p>
    <p>You probably know about webinars. You may have attended a few yourself. Perhaps you found them boring and one-way, with no chance to interact or ask questions. Out of the speaker's sight, you drifted away. Good news: we are not talking about that kind of webinar. Ours are live, engaging and built for real conversation with your audience, wherever they are. We help you choose the right tools and shape a session that people remember.</p>
    <ul>
      <li>We design an effective virtual meeting experience using every tool in the online room.</li>
      <li>We repurpose your existing materials for engaging collaborative online meetings and training.</li>
      <li>We develop and coordinate a communication plan to invite people who already follow your work.</li>
      <li>We support you "behind the scenes" so you can focus fully on delivering your content.</li>
      <li>We rehearse with you and help you show up at the day of the session ready to engage.</li>
    </ul>

    <div class="section-lead">Choose the service that best fit your needs and budget. A new level of online engagement and virtual collaboration awaits.</div>

    <div class="offer">
      <div class="offer__name">• Webinar Basics: Outfitting the Online Entrepreneur</div>
      <p>3 hours of one-on-one online coaching that gives you all you need to know about web conferencing tools, good online meeting practice and how to use them for your business. Includes access to our resource library ($450).</p>
    </div>
    <div class="offer">
      <div class="offer__name">• Fast-track CPW: Webinar Facilitator Certification in 2 weeks</div>
      <p>7 hours of one-on-one online coaching to learn about web conferencing tools and how to use them for your training sessions. Includes access to our online resource library and a month of free room use ($1,000).</p>
    </div>
    <div class="offer">
      <div class="offer__name">• "Turnkey" Solution: Your 90-minute Webinar</div>
      <p>Plan, design and implement one webinar session on the content of your expertise marketed to the audience. We build the registration process, create the session plans and coach you on delivery, with 5 hours of coaching and room access ($1,500).</p>
    </div>

    <div class="platform-note">You'll participate via the MeetSpace Live platform. No special software is required, if you have a computer with internet.</div>
    <p>As a professional communicator, whether you are a small business owner, an educator or a manager, you know that webinar technology is here to stay. Have you wondered how to use them to reach your business or your organization? Leave the details to us, then take your seat. Our personalized sessions give your business unparalleled access to new markets and potential new clients at a minimum cost.</p>
  </div>

  <div class="contact">Want to know more? Call us at 202-555-0148 or email us at hello@convergia.example</div>
</section>

</body>
</html>
```